ebook cover for The Heron & The Teapot (Plink!)

We would like an ebook cover for a post Ph.D. on Animal Totems book called The Heron and The Teapot. It is about human relationships and dating. Author is Marla Wendlow Ph.D.
I am thinking perhaps just typographic with a fancy custom italicized or handwriting kind of font that fills the whole page, or a picture that doesn't belittle the fairytale of love. Something cosmic.
The subtitle to guide people, small, is "on dating"

```html
<!DOCTYPE html>
<html lang="en">
<head>
<meta charset="utf-8">
<title>The Heron and The Teapot — On Dating</title>
<link href="https://fonts.googleapis.com/css2?family=Kaushan+Script&display=swap" rel="stylesheet">
<style>
  :root {
    --page: #ffffff;
    --paper: #fcebe2;
    --red: #f80606;
    --red-wave: #fb2a2a;
    --red-soft: #ff6161;
    --white: #fdf7f2;
  }
  html, body {
    margin: 0;
    padding: 0;
    width: 1200px;
    height: 1200px;
    overflow: hidden;
    background: var(--page);
  }
  .cover {
    position: absolute;
    left: 230px;
    top: 0;
    width: 760px;
    height: 1200px;
    background: var(--paper);
    overflow: hidden;
  }
  .title {
    position: absolute;
    inset: 0;
    margin: 0;
    font-family: "Kaushan Script", cursive;
    font-weight: 400;
    color: var(--red);
    transform: rotate(-6deg);
    transform-origin: 50% 40%;
  }
  .title span {
    position: absolute;
    display: block;
    white-space: nowrap;
    line-height: 1;
  }
  .title-the-1  { left: 400px; top: 40px;  font-size: 140px; }
  .title-heron  { left: 60px;  top: 170px; font-size: 220px; letter-spacing: -2px; }
  .title-and    { left: 250px; top: 420px; font-size: 120px; }
  .title-teapot { left: 40px;  top: 540px; font-size: 200px; letter-spacing: -2px; }
  .subtitle {
    position: absolute;
    left: 200px;
    top: 860px;
    margin: 0;
    font-family: "Kaushan Script", cursive;
    font-size: 64px;
    font-weight: 400;
    line-height: 1;
    color: var(--white);
    -webkit-text-stroke: 2px var(--red);
    transform: rotate(-6deg);
    white-space: nowrap;
  }
  .wave {
    position: absolute;
    left: 0;
    bottom: 0;
    width: 760px;
    height: 250px;
  }
  .author {
    position: absolute;
    left: 0;
    right: 0;
    top: 1090px;
    margin: 0;
    text-align: center;
    font-family: "Kaushan Script", cursive;
    font-size: 64px;
    font-weight: 400;
    line-height: 1;
    color: var(--white);
    white-space: nowrap;
  }
</style>
</head>
<body>
  <main class="cover">
    <h1 class="title" aria-label="The Heron and The Teapot">
      <span class="title-the-1">The</span>
      <span class="title-heron">Heron</span>
      <span class="title-and">and The</span>
      <span class="title-teapot">Teapot</span>
    </h1>

    <p class="subtitle">On Dating</p>

    <svg class="wave" viewBox="0 0 760 250" preserveAspectRatio="none" aria-hidden="true">
      <path d="M0 100 C 120 60, 220 40, 340 45 C 460 50, 560 20, 650 5 C 700 -5, 700 40, 690 60 C 720 90, 740 120, 760 120 L760 250 L0 250 Z" fill="var(--red-soft)"/>
      <path d="M0 115 C 110 80, 230 60, 350 65 C 470 70, 570 45, 660 25 C 690 40, 690 70, 700 90 C 720 115, 740 135, 760 140 L760 250 L0 250 Z" fill="var(--red-wave)"/>
    </svg>

    <p class="author">Marla Wendlow Ph.D</p>
  </main>
</body>
</html>
```